Business Card For Halvenmoor Financial Consulting

Hi, I would like a business card designed. Bold, modern.
Please use the same design as the logo. I have also attached the website design to see the overall theme.
Wordmark Font
Color: Hex: #01AEF7

```html
<!DOCTYPE html>
<html lang="en">
<head>
<meta charset="utf-8">
<title>Halvenmoor Financial Consulting — Business Card</title>
<link href="https://fonts.googleapis.com/css2?family=Montserrat:wght@400;500;700&display=swap" rel="stylesheet">
<style>
  :root {
    --page: #d9dadc;
    --card: #16212b;
    --accent: #01aef7;
    --edge: #2ea6e4;
    --ink: #ffffff;
    --muted: #e6ebef;
  }
  * { box-sizing: border-box; margin: 0; padding: 0; }
  html, body { width: 1200px; height: 856px; overflow: hidden; }
  body {
    background: var(--page);
    font-family: "Montserrat", sans-serif;
    display: flex;
    align-items: center;
    justify-content: center;
    gap: 40px;
  }
  .card {
    position: relative;
    width: 540px;
    height: 309px;
    background: var(--card);
    border-bottom: 4px solid var(--edge);
    box-shadow: 0 10px 24px rgba(0,0,0,.35);
    color: var(--ink);
    overflow: hidden;
  }
  .brand {
    display: flex;
    align-items: center;
    gap: 12px;
  }
  .brand-mark {
    border: 3px solid var(--accent);
    flex: none;
  }
  .brand-name {
    font-weight: 700;
    color: var(--ink);
    text-transform: uppercase;
    line-height: 1.2;
    letter-spacing: .04em;
    white-space: nowrap;
  }
  /* front */
  .card-front .brand {
    position: absolute;
    left: 28px;
    top: 170px;
    width: 226px;
  }
  .card-front .brand-mark { width: 30px; height: 30px; }
  .card-front .brand-name { font-size: 12.5px; }
  .divider {
    position: absolute;
    left: 262px;
    top: 40px;
    width: 50px;
    height: 200px;
  }
  .details {
    position: absolute;
    left: 322px;
    top: 44px;
    right: 16px;
  }
  .person-name {
    font-weight: 700;
    font-size: 19px;
    color: var(--accent);
    text-transform: uppercase;
    letter-spacing: .02em;
    white-space: nowrap;
  }
  .person-title {
    font-size: 12px;
    color: var(--muted);
    margin-top: 2px;
  }
  .address {
    font-size: 11.5px;
    color: var(--muted);
    font-style: normal;
    line-height: 1.45;
    margin-top: 16px;
  }
  .contacts {
    list-style: none;
    margin-top: 14px;
  }
  .contacts li {
    display: flex;
    align-items: center;
    gap: 8px;
    font-size: 11.5px;
    color: var(--muted);
    margin-bottom: 8px;
    white-space: nowrap;
  }
  .contacts svg { width: 16px; height: 16px; flex: none; }
  /* back */
  .card-back {
    display: flex;
    align-items: center;
    justify-content: center;
  }
  .card-back .brand { gap: 18px; }
  .card-back .brand-mark { width: 58px; height: 58px; border-width: 4px; }
  .card-back .brand-name { font-size: 24px; }
</style>
</head>
<body>
  <section class="card card-front">
    <div class="brand">
      <span class="brand-mark"></span>
      <span class="brand-name">Halvenmoor<br>Financial Consulting</span>
    </div>

    <svg class="divider" viewBox="0 0 50 200" aria-hidden="true">
      <line x1="6" y1="10" x2="6" y2="150" stroke="#01aef7" stroke-width="1"/>
      <line x1="22" y1="30" x2="22" y2="180" stroke="#01aef7" stroke-width="1"/>
      <line x1="38" y1="0" x2="38" y2="170" stroke="#01aef7" stroke-width="1"/>
    </svg>

    <div class="details">
      <h1 class="person-name">Toren Ashby</h1>
      <p class="person-title">Senior Consultant</p>
      <address class="address">44-07 Larkspur Ave 12<br>Brookvale, NY 11402</address>
      <ul class="contacts">
        <li>
          <svg viewBox="0 0 16 16" aria-hidden="true"><circle cx="8" cy="8" r="8" fill="#01aef7"/><path d="M5 4.5c.6-.4 1.2-.3 1.5.3l.6 1.2c.2.4 0 .8-.3 1l-.5.4c.4.9 1 1.5 1.9 1.9l.4-.5c.3-.3.7-.4 1-.2l1.2.6c.5.3.6.9.3 1.5-.5.8-1.5 1.1-2.4.7-2-.8-3.5-2.3-4.3-4.3-.4-.9-.2-1.9.6-2.6z" fill="#fff"/></svg>
          +1 555 014 2290
        </li>
        <li>
          <svg viewBox="0 0 16 16" aria-hidden="true"><circle cx="8" cy="8" r="8" fill="#01aef7"/><rect x="4" y="5" width="8" height="6" fill="#fff"/><path d="M4 5l4 3.2L12 5" fill="none" stroke="#01aef7" stroke-width=".9"/></svg>
          info@halvenmoor.com
        </li>
        <li>
          <svg viewBox="0 0 16 16" aria-hidden="true"><circle cx="8" cy="8" r="8" fill="#01aef7"/><circle cx="8" cy="8" r="4.2" fill="none" stroke="#fff" stroke-width="1"/><ellipse cx="8" cy="8" rx="1.8" ry="4.2" fill="none" stroke="#fff" stroke-width=".8"/><line x1="3.8" y1="8" x2="12.2" y2="8" stroke="#fff" stroke-width=".8"/></svg>
          www.halvenmoor.com
        </li>
      </ul>
    </div>
  </section>

  <section class="card card-back">
    <div class="brand">
      <span class="brand-mark"></span>
      <span class="brand-name">Halvenmoor<br>Financial Consulting</span>
    </div>
  </section>
</body>
</html>
```